Real estate broker business card

Want a modern celan but effective business card for my residential and commercial real estate business. I want the back of the card to advertise my services and to capture business. I have attached the back of my current business card fore ideas
Updates

Logos, photo and text updates added! Added Saturday, September 3, 2016

Project Deadline Extended Reason: LOGOS, PHOTOS AND TEST JUST UPLOADED! I'M READY TO PICK A DESIGN! THANK YOU! Added Saturday, September 3, 2016

Target Market(s)

home buyers and seller. commercial buyers and sellers

Industry/Entity Type

Real Estate

Contact Information for Business Card

must have my contact information and my photo

Requirements
Must have
• Carla Ventrino
• Owner & Qualifying Broker
• Ventrino Real Estate Services
• 505.718.2094
• carla@ventrinohomes.example
• www.ventrinohomes.example
Nice to have
• metallic
• Business capture text: " Don't buy or lease property without someone looking out for your best interests. I will represent you on your home or investment purchase for FREE!"
• "Home owners, call today to receive a FREE market analysis for your homes value!

```html
<!DOCTYPE html>
<html lang="en">
<head>
<meta charset="utf-8">
<title>Ventrino Real Estate Services – Business Card</title>
<link rel="stylesheet" href="https://fonts.googleapis.com/css2?family=Source+Sans+3:wght@400;600&display=swap">
<style>
  :root {
    --teal: #17899b;
    --teal-deep: #0f7283;
    --teal-light: #1f9aad;
    --paper: #f1f1f3;
    --ink-white: #ffffff;
    --backdrop: #e4e6e8;
    --photo-dark: #2b211d;
    --photo-light: #e9e6e3;
  }
  * { box-sizing: border-box; margin: 0; padding: 0; }
  html, body { width: 1200px; height: 900px; overflow: hidden; }
  body {
    background: var(--backdrop);
    font-family: "Source Sans 3", "Helvetica Neue", Arial, sans-serif;
    position: relative;
  }
  .card {
    position: absolute;
    left: 250px;
    width: 700px;
    height: 400px;
    overflow: hidden;
    box-shadow: 0 6px 18px rgba(0,0,0,0.18);
  }
  .card--front { top: 30px; background: linear-gradient(160deg, var(--teal-light), var(--teal-deep)); }
  .card--back { top: 470px; background: var(--paper); }

  .front-brand {
    position: absolute;
    left: 70px; top: 150px;
    display: flex; align-items: center; gap: 16px;
  }
  .brand-dot {
    width: 34px; height: 34px; border-radius: 50%;
    background: #c9cfd3;
  }
  .front-brand__name {
    font-size: 48px; font-weight: 600; color: #d9dee1;
    letter-spacing: 1px;
  }
  .portrait {
    position: absolute;
    right: 0; bottom: 0;
    width: 300px; height: 330px;
    border-radius: 120px 90px 0 0;
    background: linear-gradient(180deg, var(--photo-dark) 0%, #5a4136 45%, var(--photo-light) 100%);
  }

  .back-brand {
    position: absolute;
    top: 0; left: 0; right: 0; height: 220px;
    display: flex; align-items: center; justify-content: center; gap: 16px;
  }
  .brand-square {
    width: 40px; height: 40px; background: var(--teal);
  }
  .back-brand__name {
    font-size: 38px; font-weight: 600; color: var(--teal);
  }
  .back-band {
    position: absolute;
    left: 0; right: 0; bottom: 0; height: 180px;
    background: var(--teal);
    display: flex; align-items: center; justify-content: center;
    color: var(--ink-white);
  }
  .person { text-align: right; padding-right: 22px; }
  .person__name { font-size: 26px; font-weight: 600; }
  .person__title { font-size: 21px; font-weight: 400; margin-top: 2px; }
  .band-divider { width: 2px; height: 96px; background: var(--ink-white); }
  .contacts { list-style: none; padding-left: 22px; font-size: 19px; line-height: 1.55; }
  .contacts li { display: flex; align-items: center; gap: 10px; }
  .contacts svg { width: 14px; height: 14px; fill: var(--ink-white); flex: none; }
</style>
</head>
<body>

<section class="card card--front" aria-label="Card front">
  <div class="front-brand">
    <span class="brand-dot"></span>
    <span class="front-brand__name">Ventrino</span>
  </div>
  <div class="portrait" role="img" aria-label="Portrait photo of Carla Ventrino"></div>
</section>

<section class="card card--back" aria-label="Card back">
  <div class="back-brand">
    <span class="brand-square"></span>
    <span class="back-brand__name">Ventrino Real Estate Services</span>
  </div>
  <div class="back-band">
    <div class="person">
      <p class="person__name">Carla Ventrino</p>
      <p class="person__title">Owner &amp; Qualifying Broker</p>
    </div>
    <span class="band-divider"></span>
    <ul class="contacts">
      <li>
        <svg viewBox="0 0 16 16" aria-hidden="true"><path d="M3 1h3l1.5 4-2 1.3a9 9 0 0 0 4.2 4.2L11 8.5l4 1.5v3a2 2 0 0 1-2 2A12 12 0 0 1 1 3a2 2 0 0 1 2-2z"/></svg>
        505.718.2094
      </li>
      <li>
        <svg viewBox="0 0 16 16" aria-hidden="true"><path d="M1 3h14v10H1z M1 3l7 6 7-6" fill="none" stroke="#fff" stroke-width="1.6"/></svg>
        carla@ventrinohomes.example
      </li>
      <li>
        <svg viewBox="0 0 16 16" aria-hidden="true"><circle cx="8" cy="8" r="7"/></svg>
        www.ventrinohomes.example
      </li>
    </ul>
  </div>
</section>

</body>
</html>
```